International Petrochemical business needs a web design for Clearway Desk system

We need a web design for a "Clearway Desk" system for an international petrochemical company. The web site is used internally within the company. It is hosted by an internal department which provides government permit request service for other departments.

We would like to see designs of two pages using color light blue. (home page, internal page as attached).
Home Page:
1. Header has a background image and small animation. Header on home page can be taller than the header of the internal page.
2. Layout as attached.

Internal Page:
1. Header can use the same background image as the home page and can be shorter to utilize the page for content.
2. The blue icon behind every captions represent an icon. When user move mouse over this icon, it displays the caption in Thai language as a tooltip. This icon needs to be redesign.

The final design should communicate the followings:
- Excellent service provided system in terms of time and accurary
- Rapid growth of business via building petrochemical refinery plant
Updates

For Internal Page, the blue circle behind every captions represent an icon. When mouse over this icon, a tool tip showing the caption in Thai language is shown. Please also design this icon..

There are more feedbacks from customer as followed:

1. Banner should consists of 
    1.1 "Approved" stamp on paper
    1.2 An image of Garuda. It is used on every government documents in Thailand
    1.3 Image of petrochemical plant
2. Each menu item (Home, Permit, Search, etc) should have different colors. Drop down menu will use the same color as its parent menu item.
3. Overall tone of the web page should be light blue with background of the body the web page in white
4. "New Request" button should use green color with icon on it
5. Table header of each box in the body of the page should use dark blue background with text in white

Please kindly submit your revisions.
Thank you.

Industry/Entity Type

Business

Requirements
Must have
• 1. Design for 1024x768 screen resolution
2. Use light blue theme
3. Background of header where the company logo is must have white background

```html
<!DOCTYPE html>
<html lang="en">
<head>
<meta charset="utf-8">
<title>Clearway Desk – Request Form</title>
<link href="https://fonts.googleapis.com/css2?family=Roboto:wght@400;500;700;900&family=Roboto+Condensed:wght@700&display=swap" rel="stylesheet">
<style>
:root{
  --ink:#1f2b38;
  --muted:#555b62;
  --brand:#1f64b4;
  --brand-dark:#134d93;
  --nav-top:#8fd0f0;
  --nav-bot:#4fb0e0;
  --page:#b7dcf3;
  --panel:#c3e4f8;
  --panel-edge:#6fb1de;
  --head-top:#4b9be0;
  --head-bot:#1f6fc4;
  --field-line:#c3d3df;
  --chip:#b9c3cc;
  --tip:#1ba8e8;
  --link:#2a6fd6;
  --foot:#0e3a66;
}
*{box-sizing:border-box;margin:0;padding:0}
html,body{width:834px;height:1200px;overflow:hidden}
body{position:relative;font-family:"Roboto",Arial,sans-serif;background:var(--page);color:var(--ink)}
.abs{position:absolute}

.masthead{left:0;top:0;width:834px;height:66px;background:#fff}
.brand-dot{left:60px;top:17px;width:30px;height:30px;border-radius:50%;background:var(--brand)}
.brand-name{left:96px;top:22px;font:700 13px/1 "Roboto",sans-serif;color:var(--brand);width:120px;line-height:14px}
.system-title{left:255px;top:30px;font:700 27px/1 "Roboto Condensed",sans-serif;color:var(--brand);letter-spacing:.5px}

.main-nav{left:0;top:66px;width:834px;height:35px;background:linear-gradient(var(--nav-top),var(--nav-bot));border-bottom:1px solid #3a93c5}
.main-nav ul{list-style:none;display:flex;position:absolute;left:75px;top:11px;font:500 12px/1 "Roboto",sans-serif;color:#fff}
.main-nav li{margin-right:0}
.main-nav .sep{margin:0 26px}

.banner{left:0;top:101px;width:834px;height:129px;background:linear-gradient(90deg,#8c9099 0%,#d9dde2 30%,#c2c7ce 55%,#e4e7ea 75%,#7e8a8f 100%)}

.panel{left:48px;top:248px;width:758px;height:860px;border-radius:10px;background:var(--panel);border:1px solid var(--panel-edge);box-shadow:0 2px 6px rgba(0,40,90,.25);overflow:hidden}
.panel-head{left:0;top:0;width:100%;height:32px;background:linear-gradient(var(--head-top),var(--head-bot));color:#fff;font:700 14px/32px "Roboto",sans-serif;padding-left:10px}

.label{width:130px;text-align:right;font:700 11.5px/28px "Roboto",sans-serif;color:var(--ink)}
.label .req{color:#d21c1c}
.icon{width:29px;height:29px;border-radius:6px;background:linear-gradient(#ffffff,#dfe8f0);border:1px solid #9fb4c6;box-shadow:0 1px 2px rgba(0,0,0,.2)}
.icon svg{position:absolute;left:5px;top:5px}
.colon{font:700 12px/28px "Roboto",sans-serif}
.field{height:21px;background:#fff;border:1px solid var(--field-line);border-radius:4px;font:500 11.5px/19px "Roboto",sans-serif;color:#3a3f45;padding-left:8px;box-shadow:inset 0 2px 2px rgba(0,0,0,.12)}
.select::after{content:"";position:absolute;right:6px;top:6px;border:6px solid transparent;border-top:8px solid #6b7076;border-bottom:0}
.area{height:73px;border-radius:6px;padding-top:4px;box-shadow:inset 0 6px 6px rgba(0,0,0,.15)}

.btn{height:20px;border-radius:4px;background:linear-gradient(#f4f6f8,#c6ccd2);border:1px solid #98a3ad;font:700 9.5px/18px "Roboto",sans-serif;color:#707981;text-align:center;letter-spacing:.3px}
.chip{height:14px;border-radius:3px;background:var(--chip);font:700 8px/14px "Roboto",sans-serif;color:#6a737b;padding-left:5px;border:1px solid #a4afb8}
.chip b{position:absolute;right:0;top:-1px;width:14px;height:14px;background:#e9edf0;border:1px solid #a4afb8;border-radius:2px;text-align:center;font:700 8px/12px "Roboto",sans-serif;color:#333}

.tooltip{left:495px;top:362px;width:131px;height:38px;border-radius:4px;background:var(--tip);color:#fff;font:400 9px/12px "Roboto",sans-serif;padding:6px 10px}
.tooltip::before{content:"";position:absolute;left:96px;top:-6px;border:6px solid transparent;border-bottom-color:var(--tip);border-top:0}

.related{left:228px;top:932px;width:322px;height:123px;background:#fff;border-radius:5px;border:1px solid #bfd0dc;overflow:hidden}
.related table{position:absolute;left:0;top:0;width:100%;border-collapse:collapse;font:400 9.5px/14.5px "Roboto",sans-serif}
.related th{height:26px;background:linear-gradient(#fafafa,#d4d8dc);color:#5a6168;font:700 11px/26px "Roboto",sans-serif;text-align:left;padding-left:10px;border-right:1px solid #b9c1c8}
.related th:last-child{border-right:0}
.related td{padding-left:10px;color:#333;border-right:1px solid #dde3e8}
.related td:last-child{border-right:0}
.related tr.first td{padding-top:6px}
.related a{color:var(--link);text-decoration:underline}
.pager{left:115px;top:104px;width:101px;height:20px;border-radius:10px 10px 0 0;background:linear-gradient(#7ec1ee,#3c8fd6);display:flex;justify-content:center;align-items:center;gap:3px;color:#fff;font:700 8px/1 "Roboto",sans-serif}
.pager i{font-style:normal;width:11px;height:11px;border-radius:50%;background:#0e3a66;text-align:center;line-height:11px}
.pager i.on{background:#fff;color:#0e3a66}

.action{height:27px;border-radius:5px;background:linear-gradient(#fbfbfc,#c3c9cf);border:1px solid #8e99a3;font:700 12px/25px "Roboto",sans-serif;color:#6d757d;text-align:center;box-shadow:0 1px 2px rgba(0,0,0,.25)}

.site-foot{left:0;top:1128px;width:834px;height:72px;background:linear-gradient(#0d3a68,#0a2d52);color:#fff;font:400 8px/1 "Roboto",sans-serif}
</style>
</head>
<body>

<header>
  <div class="abs masthead">
    <div class="abs brand-dot"></div>
    <div class="abs brand-name">NORTHVALE<br>PETROCHEMICAL</div>
    <div class="abs system-title">CLEARWAY DESK</div>
  </div>
  <nav class="abs main-nav">
    <ul>
      <li>HOME</li><li class="sep">|</li>
      <li>PERMITS</li><li class="sep" style="margin:0 14px 0 10px">|</li>
      <li>SEARCH</li><li class="sep" style="margin:0 28px 0 22px">|</li>
      <li>REPORT</li><li class="sep" style="margin:0 26px 0 22px">|</li>
      <li>ADMIN</li><li class="sep" style="margin:0 26px 0 28px">|</li>
      <li>HELP</li>
    </ul>
  </nav>
  <div class="abs banner" role="img" aria-label="Photograph of a petrochemical plant with storage spheres, piping and railings"></div>
</header>

<main class="abs panel">
  <div class="abs panel-head">Request Form</div>

  <!-- Request date -->
  <div class="abs label" style="left:0;top:46px">Request Date</div>
  <div class="abs icon" style="left:135px;top:45px"><svg width="17" height="17" viewBox="0 0 17 17"><rect x="1" y="3" width="15" height="13" rx="2" fill="#1f64b4"/><rect x="3" y="7" width="11" height="7" fill="#fff"/><rect x="4" y="1" width="2" height="4" fill="#134d93"/><rect x="11" y="1" width="2" height="4" fill="#134d93"/></svg></div>
  <div class="abs colon" style="left:171px;top:46px">:</div>
  <div class="abs field" style="left:182px;top:50px;width:36px">21</div>
  <div class="abs field select" style="left:225px;top:50px;width:72px">January</div>
  <div class="abs field" style="left:304px;top:50px;width:46px">2013</div>

  <div class="abs label" style="left:400px;top:46px">Requester Employee No</div>
  <div class="abs icon" style="left:535px;top:45px"><svg width="17" height="17" viewBox="0 0 17 17"><circle cx="8.5" cy="8.5" r="7.5" fill="#1f64b4"/><text x="8.5" y="11.5" text-anchor="middle" font-size="7" font-weight="700" fill="#fff" font-family="Roboto,sans-serif">ID</text></svg></div>
  <div class="abs colon" style="left:571px;top:46px">:</div>
  <div class="abs field" style="left:582px;top:50px;width:148px">1200 55501 0000</div>

  <!-- Requester name -->
  <div class="abs label" style="left:0;top:82px">Requester Name</div>
  <div class="abs icon" style="left:135px;top:81px"><svg width="17" height="17" viewBox="0 0 17 17"><rect x="1" y="3" width="15" height="11" rx="2" fill="#1f64b4"/><circle cx="5.5" cy="8" r="2" fill="#fff"/><rect x="9" y="6" width="5" height="1.5" fill="#fff"/><rect x="9" y="9" width="5" height="1.5" fill="#fff"/></svg></div>
  <div class="abs colon" style="left:171px;top:82px">:</div>
  <div class="abs field" style="left:182px;top:86px;width:207px">Owen Hale</div>

  <div class="abs label" style="left:400px;top:82px">Telephone</div>
  <div class="abs icon" style="left:535px;top:81px"><svg width="17" height="17" viewBox="0 0 17 17"><path d="M4 2l3 3-2 2c1 2 3 4 5 5l2-2 3 3-2 2C8 15 2 9 2 4z" fill="#1f64b4"/></svg></div>
  <div class="abs colon" style="left:571px;top:82px">:</div>
  <div class="abs field" style="left:582px;top:86px;width:148px">2400 5550 100</div>

  <!-- Contact no -->
  <div class="abs label" style="left:0;top:118px">Contact No</div>
  <div class="abs icon" style="left:135px;top:117px"><svg width="17" height="17" viewBox="0 0 17 17"><rect x="5" y="1" width="8" height="15" rx="1.5" fill="#1f64b4"/><rect x="6.5" y="3" width="5" height="5" fill="#fff"/></svg></div>
  <div class="abs colon" style="left:171px;top:118px">:</div>
  <div class="abs field" style="left:182px;top:122px;width:207px">0800 5550 1234</div>

  <!-- Company -->
  <div class="abs label" style="left:0;top:153px">Company <span class="req">*</span></div>
  <div class="abs icon" style="left:135px;top:152px"><svg width="17" height="17" viewBox="0 0 17 17"><rect x="1" y="5" width="15" height="10" fill="#1f64b4"/><rect x="3" y="7" width="2" height="6" fill="#fff"/><rect x="7.5" y="7" width="2" height="6" fill="#fff"/><rect x="12" y="7" width="2" height="6" fill="#fff"/><rect x="1" y="2" width="15" height="2" fill="#134d93"/></svg></div>
  <div class="abs colon" style="left:171px;top:153px">:</div>
  <div class="abs field select" style="left:182px;top:157px;width:207px">Please select</div>

  <!-- Branch -->
  <div class="abs label" style="left:0;top:189px">Branch <span class="req">*</span></div>
  <div class="abs icon" style="left:135px;top:188px"><svg width="17" height="17" viewBox="0 0 17 17"><rect x="6" y="1" width="5" height="4" fill="#1f64b4"/><rect x="1" y="11" width="5" height="4" fill="#1f64b4"/><rect x="11" y="11" width="5" height="4" fill="#1f64b4"/><path d="M8.5 5v3M3.5 8h10M3.5 8v3M13.5 8v3" stroke="#1f64b4" stroke-width="1.2" fill="none"/></svg></div>
  <div class="abs colon" style="left:171px;top:189px">:</div>
  <div class="abs field select" style="left:182px;top:193px;width:207px">Please select</div>

  <!-- Document category -->
  <div class="abs label" style="left:0;top:224px">Document Category <span class="req">*</span></div>
  <div class="abs icon" style="left:135px;top:223px"><svg width="17" height="17" viewBox="0 0 17 17"><path d="M3 1h8l3 3v12H3z" fill="#fff" stroke="#1f64b4" stroke-width="1.4"/><path d="M5 9l2 2 4-4" stroke="#1f64b4" stroke-width="1.6" fill="none"/></svg></div>
  <div class="abs colon" style="left:171px;top:224px">:</div>
  <div class="abs field select" style="left:182px;top:228px;width:207px">Please select</div>

  <!-- Document type -->
  <div class="abs label" style="left:0;top:260px">Document Type <span class="req">*</span></div>
  <div class="abs icon" style="left:135px;top:259px"><svg width="17" height="17" viewBox="0 0 17 17"><path d="M3 1h8l3 3v12H3z" fill="#fff" stroke="#1f64b4" stroke-width="1.4"/><rect x="1" y="9" width="11" height="5" fill="#1f64b4"/></svg></div>
  <div class="abs colon" style="left:171px;top:260px">:</div>
  <div class="abs field select" style="left:182px;top:264px;width:207px">Please select</div>

  <!-- Expected use date -->
  <div class="abs label" style="left:0;top:295px">Expected Use Date <span class="req">*</span></div>
  <div class="abs icon" style="left:135px;top:294px"><svg width="17" height="17" viewBox="0 0 17 17"><rect x="1" y="3" width="15" height="13" rx="2" fill="#1f64b4"/><rect x="3" y="6" width="11" height="8" fill="#fff"/><text x="8.5" y="13" text-anchor="middle" font-size="7" font-weight="700" fill="#1f64b4" font-family="Roboto,sans-serif">1</text></svg></div>
  <div class="abs colon" style="left:171px;top:295px">:</div>
  <div class="abs field" style="left:182px;top:299px;width:36px">28</div>
  <div class="abs field select" style="left:225px;top:299px;width:72px">January</div>
  <div class="abs field" style="left:304px;top:299px;width:46px">2013</div>

  <!-- Detail -->
  <div class="abs label" style="left:0;top:331px">Detail <span class="req">*</span></div>
  <div class="abs icon" style="left:135px;top:330px"><svg width="17" height="17" viewBox="0 0 17 17"><rect x="1" y="2" width="12" height="14" fill="#fff" stroke="#1f64b4" stroke-width="1.4"/><path d="M4 6h6M4 9h6M4 12h3" stroke="#1f64b4" stroke-width="1.2"/><path d="M9 14l6-6 1.5 1.5-6 6z" fill="#134d93"/></svg></div>
  <div class="abs colon" style="left:171px;top:331px">:</div>
  <div class="abs field area" style="left:182px;top:331px;width:207px">Lorem ipsum dolor sit amet</div>

  <!-- Attachment -->
  <div class="abs label" style="left:0;top:419px">Attachment</div>
  <div class="abs icon" style="left:135px;top:418px"><svg width="17" height="17" viewBox="0 0 17 17"><path d="M12 6l-5 5a1.5 1.5 0 0 1-2-2l6-6a3 3 0 0 1 4 4l-7 7a4 4 0 0 1-6-6l5-5" stroke="#1f64b4" stroke-width="1.5" fill="none"/></svg></div>
  <div class="abs colon" style="left:171px;top:419px">:</div>
  <div class="abs field" style="left:182px;top:423px;width:207px">confidential.doc</div>
  <div class="abs btn" style="left:395px;top:423px;width:59px">BROWSE</div>
  <div class="abs btn" style="left:461px;top:423px;width:59px">ATTACH</div>
  <div class="abs chip" style="left:183px;top:448px;width:61px">file1.doc<b>X</b></div>
  <div class="abs chip" style="left:250px;top:448px;width:63px">file1.doc<b>X</b></div>
  <div class="abs chip" style="left:319px;top:448px;width:62px">file1.doc<b>X</b></div>

  <!-- Coordinator -->
  <div class="abs label" style="left:0;top:472px">Coordinator <span class="req">*</span></div>
  <div class="abs icon" style="left:135px;top:471px"><svg width="17" height="17" viewBox="0 0 17 17"><circle cx="8.5" cy="5" r="3.5" fill="#1f64b4"/><path d="M2 16c0-4 3-6 6.5-6S15 12 15 16z" fill="#1f64b4"/></svg></div>
  <div class="abs colon" style="left:171px;top:472px">:</div>
  <div class="abs btn" style="left:183px;top:476px;width:59px">ADD</div>
  <div class="abs chip" style="left:183px;top:501px;width:89px">Owen Hale HR<b>X</b></div>

  <!-- Related person -->
  <div class="abs label" style="left:0;top:526px">Related Person <span class="req">*</span></div>
  <div class="abs icon" style="left:135px;top:525px"><svg width="17" height="17" viewBox="0 0 17 17"><circle cx="5.5" cy="6" r="3" fill="#1f64b4"/><circle cx="11.5" cy="6" r="3" fill="#1f64b4"/><path d="M0 15c0-3 2.5-5 5.5-5s5.5 2 5.5 5zM6 15c0-3 2.5-5 5.5-5S17 12 17 15z" fill="#1f64b4"/></svg></div>
  <div class="abs colon" style="left:171px;top:526px">:</div>
  <div class="abs btn" style="left:183px;top:529px;width:59px">ADD</div>
  <div class="abs chip" style="left:183px;top:551px;width:88px">Nina Park (IT)<b>X</b></div>
  <div class="abs chip" style="left:277px;top:551px;width:106px">Ted Lowe (Finance)<b>X</b></div>
  <div class="abs chip" style="left:183px;top:568px;width:112px">Ray Dunn (Finance)<b>X</b></div>

  <!-- Remark -->
  <div class="abs label" style="left:0;top:597px">Remark</div>
  <div class="abs icon" style="left:135px;top:596px"><svg width="17" height="17" viewBox="0 0 17 17"><rect x="1" y="3" width="15" height="10" rx="2" fill="#1f64b4"/><circle cx="5" cy="8" r="1" fill="#fff"/><circle cx="8.5" cy="8" r="1" fill="#fff"/><circle cx="12" cy="8" r="1" fill="#fff"/></svg></div>
  <div class="abs colon" style="left:171px;top:597px">:</div>
  <div class="abs field area" style="left:182px;top:596px;width:207px;height:71px">Lorem ipsum dolor sit amet</div>

  <!-- Related request -->
  <div class="abs label" style="left:0;top:685px">Related Request</div>
  <div class="abs icon" style="left:135px;top:684px"><svg width="17" height="17" viewBox="0 0 17 17"><ellipse cx="7" cy="6" rx="6" ry="4" fill="#1f64b4"/><ellipse cx="11" cy="10" rx="5" ry="3.5" fill="#134d93"/><path d="M4 9l-2 4 4-2z" fill="#1f64b4"/></svg></div>
  <div class="abs colon" style="left:171px;top:685px">:</div>
</main>

<div class="abs tooltip" lang="th">ระหว่างดำเนินการรอดำเนินก ารรอดำเนินการ</div>

<section class="abs related">
  <table>
    <tr><th style="width:87px">Request No.</th><th style="width:87px">Request Date</th><th style="width:69px">Company</th><th>Branch</th></tr>
    <tr class="first"><td><a>AB56001</a></td><td>20/4/2013</td><td>NVP</td><td>GC1</td></tr>
    <tr><td><a>BIO5502</a></td><td>21/4/2013</td><td>NVP</td><td>GC2</td></tr>
    <tr><td><a>AB56001</a></td><td>20/4/2013</td><td>QRS</td><td>GC3</td></tr>
    <tr><td><a>BIO5502</a></td><td>21/4/2013</td><td>QRS</td><td>GC4</td></tr>
  </table>
  <div class="abs pager"><span>&lsaquo;</span><i class="on">1</i><i>2</i><i>3</i><i>4</i><i>5</i><span>&rsaquo;</span></div>
</section>

<div class="abs action" style="left:228px;top:1064px;width:92px;text-align:left;padding-left:46px">BACK</div>
<svg class="abs" style="left:228px;top:1065px" width="36" height="26" viewBox="0 0 36 26"><rect x="0" y="0" width="36" height="25" rx="4" fill="#d4d9de"/><path d="M21 7l-6 6 6 6" stroke="#3a4047" stroke-width="2.5" fill="none"/></svg>
<div class="abs action" style="left:327px;top:1064px;width:222px">CREATE NEW REQUEST</div>

<footer class="abs site-foot">
  <div class="abs" style="left:61px;top:15px">Copyright © 2013 NorthvalePetrochemical. All rights reserved.</div>
  <div class="abs" style="left:690px;top:15px">Terms and Condition | Privacy</div>
</footer>

</body>
</html>
```